Flight school sign for building, banner, and bilboard

This sign is primarily for use on the side of our flight school building to draw attention for current and future flight school students. We offer airplane and helicopter flight training, ground school training and seminars, airplane and helicopter rentals, multi-engine training, and more. I would like a professional but exciting sign that can be used across a multitude of signage options such as banners, banner ads, billboard, and other mediums so that our sign is consistent and recognizable.

Contact Information for Business Card

The business card should match our company sign somewhat but not exactly. We want good and exciting imagery or wording and energizing/exciting colors.

```html
<!DOCTYPE html>
<html lang="en">
<head>
<meta charset="utf-8">
<title>Zenith Aviation – Flight School Sign</title>
<link rel="stylesheet" href="https://fonts.googleapis.com/css2?family=Anton&family=Oswald:wght@500;600&family=Rubik:wght@500&display=swap">
<style>
  :root {
    --navy: #272a68;
    --red: #e8293b;
    --white: #ffffff;
    --backdrop: #e6e7ea;
    --sky: #a9aeb8;
    --field: #6e8652;
    --grass: #55703d;
  }
  html, body {
    margin: 0;
    width: 1000px;
    height: 1200px;
    overflow: hidden;
    background: var(--backdrop);
  }
  .sign {
    position: absolute;
    left: 20px;
    top: 432px;
    width: 960px;
    height: 336px;
    box-shadow: 0 10px 30px rgba(0,0,0,0.25);
  }
  .sign svg { display: block; width: 100%; height: 100%; }
  .brand-name { font-family: "Rubik", sans-serif; font-weight: 500; fill: var(--white); letter-spacing: 1px; }
  .service { font-family: "Oswald", sans-serif; font-weight: 600; fill: var(--white); font-size: 30px; letter-spacing: 0.5px; }
  .chevron { fill: none; stroke: var(--red); stroke-width: 5; }
  .headline { font-family: "Anton", sans-serif; paint-order: stroke; stroke-linejoin: round; }
  .headline-top { fill: var(--navy); stroke: var(--white); stroke-width: 4; font-size: 74px; }
  .headline-main { fill: var(--red); stroke: var(--navy); stroke-width: 5; font-size: 112px; }
  .contact { font-family: "Rubik", sans-serif; font-weight: 500; font-size: 46px; }
  .contact-web { fill: var(--red); }
  .contact-phone { fill: var(--white); }
</style>
</head>
<body>
<div class="sign">
  <svg viewBox="0 0 1573 550" xmlns="http://www.w3.org/2000/svg">
    <defs>
      <linearGradient id="photoTone" x1="0" y1="0" x2="0" y2="1">
        <stop offset="0" stop-color="var(--sky)"/>
        <stop offset="0.45" stop-color="#99a09a"/>
        <stop offset="0.7" stop-color="var(--field)"/>
        <stop offset="1" stop-color="var(--grass)"/>
      </linearGradient>
    </defs>

    <!-- base -->
    <rect class="sign-base" width="1573" height="550" fill="var(--navy)"/>

    <!-- photo panel -->
    <path class="photo-panel" role="img" aria-label="Photo of an orange and white trainer aircraft taxiing on a grass airfield"
      d="M500 0 L1340 0 C1480 80 1560 250 1500 400 C1460 490 1350 510 1220 500 C1120 490 1060 470 1000 430 Z"
      fill="url(#photoTone)" stroke="var(--navy)" stroke-width="4"/>
    <line class="accent-line" x1="690" y1="160" x2="1200" y2="550" stroke="var(--white)" stroke-width="4"/>

    <!-- red swoosh and contact band -->
    <path class="swoosh" fill="var(--red)"
      d="M1395 45 C1500 110 1573 230 1573 330 L1573 550 L545 550 L598 460 L1100 460 C1200 520 1380 520 1470 470 C1570 400 1560 170 1395 45 Z"/>
    <path class="web-band" fill="var(--white)" d="M0 460 L600 460 L548 550 L0 550 Z"/>

    <!-- airplane graphic area -->
    <rect class="plane-graphic" role="img" aria-label="Red airplane graphic climbing to the upper left"
      x="505" y="8" width="185" height="155" rx="14" fill="var(--red)"/>

    <!-- brand -->
    <circle class="brand-dot" cx="280" cy="100" r="48" fill="var(--white)"/>
    <text class="brand-name" x="280" y="215" font-size="40" text-anchor="middle">ZENITH AVIATION</text>

    <!-- services -->
    <g class="services">
      <polyline class="chevron" points="62,275 72,285 62,295"/><polyline class="chevron" points="74,275 84,285 74,295"/>
      <text class="service" x="95" y="295">AIRPLANE AND</text>
      <text class="service" x="95" y="335">HELICOPTER FLIGHT TRAINING</text>

      <polyline class="chevron" points="62,370 72,380 62,390"/><polyline class="chevron" points="74,370 84,380 74,390"/>
      <text class="service" x="95" y="390">AIRPLANE AND</text>
      <text class="service" x="95" y="430">HELICOPTER RENTALS</text>

      <polyline class="chevron" points="452,275 462,285 452,295"/><polyline class="chevron" points="464,275 474,285 464,295"/>
      <text class="service" x="485" y="295">GROUND SCHOOL</text>
      <text class="service" x="485" y="335">TRAINING AND SEMINARS</text>

      <polyline class="chevron" points="452,372 462,382 452,392"/><polyline class="chevron" points="464,372 474,382 464,392"/>
      <text class="service" x="485" y="393">MULTI-ENGINE TRAINING,</text>
      <text class="service" x="485" y="433">AND MORE.</text>
    </g>

    <!-- headline -->
    <text class="headline headline-top" x="762" y="100" textLength="490" lengthAdjust="spacingAndGlyphs">EXCELLENCE IN</text>
    <text class="headline headline-main" x="760" y="200" textLength="492" lengthAdjust="spacingAndGlyphs">AVIATION</text>

    <!-- contact -->
    <g class="globe-icon" fill="none" stroke="var(--navy)" stroke-width="3">
      <circle cx="79" cy="503" r="15"/>
      <ellipse cx="79" cy="503" rx="7" ry="15"/>
      <line x1="64" y1="503" x2="94" y2="503"/>
      <path d="M67 494 H91 M67 512 H91"/>
    </g>
    <text class="contact contact-web" x="112" y="520">ZenithAviation.com</text>

    <g class="phone-icon" fill="none" stroke="var(--white)" stroke-width="3">
      <circle cx="638" cy="505" r="19"/>
      <path d="M631 494 L635 492 L638 499 L635 502 C636 507 639 510 643 512 L646 509 L652 512 L650 516 C640 517 629 505 631 494 Z" fill="var(--white)" stroke-width="1"/>
    </g>
    <text class="contact contact-phone" x="677" y="522">(205) 555 0142</text>
  </svg>
</div>
</body>
</html>
```